Corporate Business Card

Very professional, Modern, Not to busy, include phone address email, website
(253) 617-4930, 18761 52nd Avenue S, Kent, WA 98047, martin@plumlinegroup.com, varkoworks.com

Target Market(s)

Manufacturing

Industry/Entity Type

Aero, machining, manufacturing, Off road racing

Contact Information for Business Card

Phone, address email, website

```html
<!DOCTYPE html>
<html lang="en">
<head>
<meta charset="utf-8">
<title>Varko Works – Business Card</title>
<link rel="stylesheet" href="https://fonts.googleapis.com/css2?family=Saira:wght@400;500;700&display=swap">
<style>
  :root {
    --backdrop: #1c1d20;
    --brand-red: #d4232e;
    --brand-navy: #17346d;
    --paper: #ffffff;
    --ink-light: #ffffff;
  }
  * { box-sizing: border-box; margin: 0; padding: 0; }
  html, body {
    width: 1200px; height: 786px; overflow: hidden;
    background: var(--backdrop);
    font-family: "Saira", Arial, sans-serif;
  }
  .canvas { position: relative; width: 1200px; height: 786px; }
  .card {
    position: absolute; top: 245px;
    width: 520px; height: 297px;
    overflow: hidden;
    box-shadow: 0 14px 30px rgba(0,0,0,.55);
  }
  .card-front { left: 55px; background: var(--brand-red); }
  .card-back { left: 625px; background: var(--paper); }

  .front-wordmark {
    position: absolute; left: 0; right: 0; top: 108px;
    text-align: center; color: var(--ink-light);
    font-weight: 700; font-size: 44px; letter-spacing: 3px; line-height: 1;
  }
  .front-rule {
    position: absolute; left: 150px; width: 220px; top: 172px;
    height: 2px; background: var(--ink-light);
  }

  .back-shapes { position: absolute; inset: 0; width: 100%; height: 100%; }
  .back-wordmark {
    position: absolute; left: 210px; top: 40px;
    color: var(--brand-navy);
    font-weight: 700; font-size: 24px; letter-spacing: 1.5px; line-height: 1;
    white-space: nowrap;
  }
  .back-rule {
    position: absolute; left: 210px; top: 74px; width: 140px;
    height: 2px; background: var(--brand-navy);
  }
  .contact {
    position: absolute; left: 34px; top: 150px;
    color: var(--ink-light);
  }
  .contact-name { font-weight: 700; font-size: 17px; letter-spacing: 1px; line-height: 1.1; }
  .contact-title { font-size: 11px; line-height: 1.3; margin-bottom: 8px; }
  .contact-list { list-style: none; font-size: 10px; line-height: 1.4; }
  .contact-list li { display: flex; align-items: flex-start; gap: 7px; }
  .contact-list svg { width: 10px; height: 10px; margin-top: 2px; flex: none; fill: var(--ink-light); }
</style>
</head>
<body>
<main class="canvas">
  <section class="card card-front" aria-label="Card front">
    <div class="front-wordmark">VARKO WORKS</div>
    <div class="front-rule"></div>
  </section>

  <section class="card card-back" aria-label="Card back">
    <svg class="back-shapes" viewBox="0 0 520 297" preserveAspectRatio="none" aria-hidden="true">
      <polygon points="0,140 470,98 470,297 0,297" fill="var(--brand-navy)"/>
      <polygon points="448,0 520,0 520,297 415,297" fill="var(--brand-red)"/>
    </svg>
    <div class="back-wordmark">VARKO WORKS</div>
    <div class="back-rule"></div>

    <div class="contact">
      <div class="contact-name">DANIEL PRUITT</div>
      <div class="contact-title">Managing Director</div>
      <ul class="contact-list">
        <li>
          <svg viewBox="0 0 10 10"><path d="M5 0a3.5 3.5 0 0 0-3.5 3.5C1.5 6 5 10 5 10s3.5-4 3.5-6.5A3.5 3.5 0 0 0 5 0zm0 5a1.4 1.4 0 1 1 0-2.8A1.4 1.4 0 0 1 5 5z"/></svg>
          <span>18761 52nd Avenue S<br>Kent, WA 98047</span>
        </li>
        <li>
          <svg viewBox="0 0 10 10"><path d="M2 0.5l2 2-1 1.2a6 6 0 0 0 3.3 3.3l1.2-1 2 2-1.2 1.5C4.5 9.5 0.5 5.5 0.5 1.7z"/></svg>
          <span>(253) 617-4930</span>
        </li>
        <li>
          <svg viewBox="0 0 10 10"><path d="M0 2h10v6H0z M0.6 2.4L5 5.6l4.4-3.2" fill="none" stroke="#fff" stroke-width="1"/></svg>
          <span>martin@plumlinegroup.com</span>
        </li>
        <li>
          <svg viewBox="0 0 10 10"><circle cx="5" cy="5" r="4.3" fill="none" stroke="#fff" stroke-width="1"/><path d="M0.7 5h8.6M5 0.7c-2.4 2.6-2.4 6 0 8.6M5 0.7c2.4 2.6 2.4 6 0 8.6" fill="none" stroke="#fff" stroke-width=".8"/></svg>
          <span>www.varkoworks.com</span>
        </li>
      </ul>
    </div>
  </section>
</main>
</body>
</html>
```